Volbrey Inc Business Card

Looking to get an updated business card for a Contract Machining company (www.volbreyinc.example) - looking for a clean design the portrays the technical nature of the business - colors can follow the website design and be in any combination that makes sense (red black, white, metallic or silver) - logos attached for use also. Would like space for: Name, title, business phone (555 214-3086), cell phone , website (www.volbreyinc.example) - possibly QR code could be integrated for website (designer choice), business address - 418 Harlow Bend, Carrowfield, OH 44199 (cards will be for 4 employees, I will either need to modify a template or I can provide individual information)
Target Market(s)
Aerospace, defense and medical device manufacturing companies that need machining
Industry/Entity Type
Machining for aerospace, defense, medical
Contact Information for Business Card
Name, Title, Business Phone, Cell Phone, email, business website and business address
Look and feel

```html
<!DOCTYPE html>
<html lang="en">
<head>
<meta charset="utf-8">
<title>Volbrey Inc Business Card</title>
<link rel="stylesheet" href="https://fonts.googleapis.com/css2?family=Montserrat:wght@400;700;800&display=swap">
<style>
  :root {
    --backdrop: #3a3633;
    --card-black: #1b1b1c;
    --card-back: #141414;
    --brand-red: #b93236;
    --text-white: #f2f2f2;
  }
  * { box-sizing: border-box; margin: 0; padding: 0; }
  html, body {
    width: 1200px; height: 900px; overflow: hidden;
    background: var(--backdrop);
    font-family: "Montserrat", sans-serif;
  }
  .canvas { position: relative; width: 1200px; height: 900px; }

  .card {
    position: absolute; left: 250px; width: 700px; height: 400px;
    box-shadow: 0 10px 30px rgba(0,0,0,.45);
    overflow: hidden;
  }
  .card--back { top: 30px; background: var(--card-back); }
  .card--front { top: 470px; background: var(--card-black); }

  /* back side */
  .back-texture {
    position: absolute; inset: 0;
    background: radial-gradient(circle at 50% 50%, #1d1d1d 0%, #121212 70%);
  }
  .back-mark {
    position: absolute; left: 50%; top: 50%; transform: translate(-50%, -50%);
    display: flex; align-items: center; gap: 14px;
  }
  .brand-dot {
    width: 56px; height: 56px; border-radius: 50%; background: var(--brand-red);
  }
  .brand-name {
    font-weight: 800; color: var(--brand-red); letter-spacing: 2px;
    text-transform: uppercase; white-space: nowrap;
  }
  .back-mark .brand-name { font-size: 26px; }

  /* front side */
  .front-mark {
    position: absolute; left: 250px; top: 40px; width: 210px;
    display: flex; flex-direction: column; align-items: center; gap: 14px;
  }
  .front-mark .brand-dot { width: 118px; height: 118px; }
  .front-mark .brand-name { font-size: 30px; }

  .person {
    position: absolute; right: 362px; top: 236px; text-align: right;
    white-space: nowrap;
  }
  .person-name {
    font-weight: 800; font-size: 27px; color: var(--brand-red);
    letter-spacing: 1px; text-transform: uppercase;
  }
  .person-title {
    font-weight: 400; font-size: 18px; color: var(--text-white); margin-top: 4px;
  }
  .divider {
    position: absolute; left: 352px; top: 222px; width: 2px; height: 84px;
    background: linear-gradient(var(--brand-red), rgba(185,50,54,.2));
  }
  .contacts {
    position: absolute; left: 372px; top: 216px; list-style: none;
    color: var(--text-white); font-size: 17px; white-space: nowrap;
  }
  .contacts li { display: flex; align-items: center; gap: 10px; height: 32px; }
  .contacts svg { width: 20px; height: 20px; flex: none; }

  .address-band {
    position: absolute; left: 0; right: 0; top: 318px; height: 46px;
    background: var(--brand-red); color: var(--text-white);
    display: flex; align-items: center; padding-left: 150px;
    font-size: 19px; font-weight: 400; white-space: nowrap;
  }
</style>
</head>
<body>
<div class="canvas">

  <section class="card card--back" aria-label="Card back">
    <div class="back-texture" role="img" aria-label="Embossed repeating pattern of the company emblem in black on black"></div>
    <div class="back-mark">
      <span class="brand-dot"></span>
      <span class="brand-name">Volbrey</span>
    </div>
  </section>

  <section class="card card--front" aria-label="Card front">
    <div class="front-mark">
      <span class="brand-dot"></span>
      <span class="brand-name">Volbrey</span>
    </div>

    <div class="person">
      <p class="person-name">Marcus Dellwyn</p>
      <p class="person-title">Managing Director</p>
    </div>

    <span class="divider"></span>

    <ul class="contacts">
      <li>
        <svg viewBox="0 0 24 24" fill="#b93236" aria-hidden="true"><path d="M6.6 10.8a15.1 15.1 0 0 0 6.6 6.6l2.2-2.2a1 1 0 0 1 1-.25 11.4 11.4 0 0 0 3.6.57 1 1 0 0 1 1 1V20a1 1 0 0 1-1 1A17 17 0 0 1 3 4a1 1 0 0 1 1-1h3.5a1 1 0 0 1 1 1c0 1.25.2 2.45.57 3.57a1 1 0 0 1-.25 1z"/></svg>
        (555 214-3086)
      </li>
      <li>
        <svg viewBox="0 0 24 24" fill="none" stroke="#b93236" stroke-width="2" aria-hidden="true"><rect x="7" y="2" width="10" height="20" rx="2"/><line x1="11" y1="18" x2="13" y2="18"/></svg>
        (555 214-3086)
      </li>
      <li>
        <svg viewBox="0 0 24 24" aria-hidden="true"><circle cx="12" cy="12" r="10" fill="#b93236"/><path d="M2 12h20M12 2c3 3 3 17 0 20M12 2c-3 3-3 17 0 20" stroke="#1b1b1c" stroke-width="1.4" fill="none"/></svg>
        www.volbreyinc.example
      </li>
    </ul>

    <div class="address-band">418 Harlow Bend, Carrowfield, OH 44199</div>
  </section>

</div>
</body>
</html>
```